Business Card Design Project

We are a construction company in Orange County, CA. We need a two sided business card. We would like the back to be our logo with web URL. Front should included Name, title, address, phone, fax and email address.

our address is
627 West Dorrance Blvd, Suite 308
Westhaven, AZ 92718

Our logo files are attached.

Construction

```html
<!DOCTYPE html>
<html lang="en">
<head>
<meta charset="utf-8">
<title>Corvane Business Card</title>
<link href="https://fonts.googleapis.com/css2?family=Lato:wght@400;700&display=swap" rel="stylesheet">
<style>
  :root {
    --brand-blue: #1b4a7e;
    --ink-grey: #6b6b6b;
    --card-white: #ffffff;
    --page-bg: #ececec;
    --rule-grey: #c9c9c9;
  }
  * { margin: 0; padding: 0; box-sizing: border-box; }
  html, body { width: 1200px; height: 444px; overflow: hidden; }
  body {
    background: var(--page-bg);
    font-family: "Lato", Arial, sans-serif;
    position: relative;
  }
  .card {
    position: absolute;
    top: 75px;
    width: 514px;
    height: 294px;
    border-radius: 12px;
    overflow: hidden;
  }
  .card-front { left: 74px; background: var(--card-white); }
  .card-back { left: 612px; background: var(--brand-blue); }

  .wordmark {
    font-weight: 700;
    letter-spacing: -1px;
    line-height: 1;
  }
  .card-front .wordmark {
    position: absolute;
    left: 32px;
    top: 64px;
    font-size: 60px;
    color: var(--brand-blue);
  }
  .card-back .wordmark {
    position: absolute;
    left: 0; right: 0;
    top: 96px;
    text-align: center;
    font-size: 56px;
    color: var(--card-white);
  }
  .holder {
    position: absolute;
    left: 32px;
    top: 188px;
    display: flex;
    align-items: center;
  }
  .holder-name {
    font-weight: 700;
    font-size: 17px;
    color: var(--brand-blue);
    padding-right: 7px;
    border-right: 1px solid var(--rule-grey);
    line-height: 22px;
  }
  .holder-title {
    font-size: 13px;
    color: var(--ink-grey);
    padding-left: 7px;
  }
  .divider {
    position: absolute;
    left: 150px;
    right: 0;
    top: 216px;
    height: 3px;
    background: linear-gradient(to right, rgba(180,180,180,0), #bdbdbd 60%, #9a9a9a);
  }
  .contact-band {
    position: absolute;
    left: 0; right: 0; bottom: 0;
    height: 75px;
    background: var(--brand-blue);
    color: var(--card-white);
    padding: 16px 0 0 32px;
    font-size: 13px;
  }
  .contact-row { display: flex; align-items: center; gap: 8px; white-space: nowrap; }
  .contact-item { display: flex; align-items: center; gap: 3px; }
  .contact-item svg { width: 10px; height: 10px; fill: var(--card-white); }
  .address { margin-top: 9px; }
  .web-url {
    position: absolute;
    left: 0; right: 0;
    top: 246px;
    text-align: center;
    color: var(--card-white);
    font-size: 12px;
    letter-spacing: 2.5px;
  }
</style>
</head>
<body>
  <section class="card card-front" aria-label="Business card front">
    <div class="wordmark">CORVANE</div>
    <div class="holder">
      <span class="holder-name">YOUR NAME</span>
      <span class="holder-title">Title</span>
    </div>
    <div class="divider"></div>
    <div class="contact-band">
      <div class="contact-row">
        <span class="contact-item">
          <svg viewBox="0 0 10 10" aria-hidden="true"><path d="M2 0.5 L3.6 2.6 L2.8 3.6 C3.4 5 5 6.6 6.4 7.2 L7.4 6.4 L9.5 8 L8.4 9.5 C4.5 9.3 0.7 5.5 0.5 1.6 Z"/></svg>
          0412550198
        </span>
        <span class="contact-item">
          <svg viewBox="0 0 10 10" aria-hidden="true"><rect x="2.5" y="0.5" width="5" height="3"/><rect x="0.5" y="3.5" width="9" height="4.5" rx="1"/><rect x="2.5" y="6.5" width="5" height="3" fill="#1b4a7e" stroke="#fff" stroke-width="0.8"/></svg>
          0412550199
        </span>
        <span class="contact-item">
          <svg viewBox="0 0 10 10" aria-hidden="true"><path d="M0.5 2 H9.5 V8 H0.5 Z M1 2.5 L5 5.5 L9 2.5" stroke="#1b4a7e" stroke-width="0.8"/></svg>
          info@corvane.com
        </span>
        <span class="contact-item">
          <svg viewBox="0 0 10 10" aria-hidden="true"><circle cx="5" cy="5" r="4.5"/><path d="M0.5 5 H9.5 M5 0.5 C3 3 3 7 5 9.5 M5 0.5 C7 3 7 7 5 9.5" stroke="#1b4a7e" stroke-width="0.8" fill="none"/></svg>
          www.corvane.com
        </span>
      </div>
      <div class="address">627 West Dorrance Blvd, Suite 308 Westhaven, AZ 92718</div>
    </div>
  </section>

  <section class="card card-back" aria-label="Business card back">
    <div class="wordmark">CORVANE</div>
    <div class="web-url">www.corvane.com</div>
  </section>
</body>
</html>
```